Brief 1.
An Overview / Background of the Business & Services-
It is a new business being set up. Our business is to design a solution to enable Alumni of higher institutions in Nigeria apply for their academic transcript through our system. the name of our product will be Record Relay Nigeria. We need logo, site banner, advert banner and several academic images. See www.rrly-ng.example for more insight.
The Target Market / Audience you are trying to reach-
Alumni of Nigeria Universities, usually between the ages of 20-40.
Design Specifics; any preferences or ideas for Style, Colour, Imagery, etc-
Color scheme will be several shades of light blue and white. Please check www.rrly-ng.example for more insight.

Brief 2

Pantrybasket.com is an online food and grocery shop, we supply fresh food stuff and other daily essential needs on request to customers. The site is already up (www.pantrybasket.example). We need logo, site rolling banner, advert banner and several offer graphics as shown in the placeholder images in the site now.
Working women in Nigeria.
Color scheme will be several shades of light Green and White. Please check the site.

```html
<!DOCTYPE html>
<html lang="en">
<head>
<meta charset="utf-8">
<title>Fresh Pantry – Pantrybasket.com</title>
<link href="https://fonts.googleapis.com/css2?family=Bitter:wght@700&family=Comfortaa:wght@400;700&family=Open+Sans:wght@400;600;700&display=swap" rel="stylesheet">
<style>
:root{
  --green:#7dc043;
  --green-dark:#5a9a2a;
  --green-light:#a9d86e;
  --teal:#4fb3c9;
  --text:#555;
  --muted:#888;
  --line:#e2e2e2;
  --bg:#f4f4f4;
  --white:#fff;
}
*{box-sizing:border-box;margin:0;padding:0}
html,body{width:721px;height:1200px;overflow:hidden}
body{background:var(--bg);font-family:"Open Sans",sans-serif;color:var(--text);position:relative;font-size:8px}
.abs{position:absolute}
.brand{left:72px;top:14px;font-family:"Comfortaa",sans-serif;font-weight:700;font-size:21px;color:var(--green);display:flex;align-items:center;gap:6px}
.brand-dot{width:12px;height:12px;border-radius:50%;background:var(--green)}
.search{left:294px;top:24px;width:130px;height:20px;border:1px solid #ccc;background:var(--white);font-size:7px;color:var(--muted);padding:5px 6px}
.search svg{position:absolute;right:4px;top:4px}
.cart-top{left:542px;top:32px;font-size:7px;color:var(--teal);display:flex;align-items:center;gap:3px}
.cart-top b{color:#444}
.nav{left:44px;top:64px;width:596px;height:30px;background:var(--green);display:flex;align-items:center;gap:20px;padding-left:32px;clip-path:polygon(0 0,98% 0,100% 50%,98% 100%,0 100%,2% 50%)}
.nav a{font-family:"Bitter",serif;color:var(--white);font-size:8px;text-decoration:none}
.welcome{left:67px;top:96px;width:563px;height:18px;background:var(--white);border:1px solid var(--line);font-size:7px;display:flex;justify-content:space-between;align-items:center;padding:0 8px}
.panel{left:67px;top:130px;width:563px;height:930px;background:var(--white);border:1px solid var(--line)}
.photo{position:absolute}
.hero{left:77px;top:138px;width:397px;height:226px;background:linear-gradient(135deg,#6b9a3a,#8a4a2a 40%,#5a2e1a 70%,#a8c46a)}
.hero-cap{left:77px;top:155px;width:300px;height:38px;background:rgba(255,255,255,.85)}
.hero-cap h2{font-family:"Comfortaa",sans-serif;font-weight:400;color:var(--green);font-size:17px;padding:4px 0 0 16px}
.hero-cap p{font-size:7px;color:#333;padding-left:16px}
.badge{left:356px;top:148px;width:56px;height:56px;border-radius:50%;background:var(--green);color:var(--white);font-family:"Comfortaa",sans-serif;font-size:15px;display:flex;align-items:center;justify-content:center}
.dots{left:438px;top:350px;display:flex;gap:3px}
.dots i{width:7px;height:7px;border-radius:50%;background:var(--green)}
.side1{left:478px;top:138px;width:141px;height:112px;background:linear-gradient(180deg,#f5a623,#f7c85a 45%,#fbbc3a)}
.side1-text{left:478px;top:164px;width:141px;height:62px;background:rgba(220,238,190,.9);font-family:"Comfortaa",sans-serif;color:var(--green-dark);font-size:9px;padding:4px 3px;line-height:20px}
.side1-text b{font-size:11px}
.side2{left:478px;top:253px;width:141px;height:110px;background:linear-gradient(135deg,#3f8a2a,#7cba4a 60%,#c9a27a)}
.side2-cap{left:478px;top:341px;width:141px;height:22px;background:rgba(125,192,67,.9);color:var(--white);font-family:"Comfortaa",sans-serif;font-size:7px;padding:6px 3px}
.side-h{left:67px;width:129px;height:20px;background:var(--green);color:var(--white);font-family:"Bitter",serif;font-size:8px;padding:5px 11px;clip-path:polygon(0 0,95% 0,100% 50%,95% 100%,0 100%)}
.side-h.teal{background:var(--teal)}
.cats{left:78px;top:414px;width:113px;list-style:none;font-size:7px}
.cats li{height:17.6px;border-bottom:1px solid var(--line);display:flex;justify-content:space-between;align-items:center;padding-left:2px}
.side-note{left:84px;width:110px;font-size:7px;line-height:11px}
.offer{left:78px;top:692px;width:118px;height:152px;background:linear-gradient(180deg,#8ac34e,#c8a060 45%,#e8c25a 75%,#a0c060)}
.offer-h{left:78px;top:692px;width:118px;height:30px;background:var(--green);color:var(--white);font-family:"Comfortaa",sans-serif;font-size:9px;padding:7px 6px;border-radius:0 0 40% 0}
.offer-pct{left:154px;top:812px;width:42px;height:32px;background:var(--green);color:var(--white);font-family:"Comfortaa",sans-serif;font-size:12px;border-radius:30px 0 0 0;padding:10px 0 0 12px}
.mini{left:82px;display:flex;gap:6px;font-size:7px;line-height:11px}
.mini .thumb{width:26px;height:26px;border:1px solid var(--line);background:linear-gradient(135deg,#9aa6ae,#5b6770);margin-top:4px}
.mini .price{font-size:6px}
.sec-h{font-family:"Bitter",serif;color:var(--green-dark);font-size:8px}
.arrows{left:588px;top:388px;display:flex;gap:4px}
.arrows i{width:10px;height:10px;border-radius:50%;background:#bbb;display:flex;align-items:center;justify-content:center}
.card{position:absolute;width:129px;background:var(--white);border:3px solid #e8e8e8;text-align:center;overflow:hidden}
.card .ribbon{position:absolute;left:-14px;top:6px;transform:rotate(-45deg);width:50px;font-size:6px;color:#333;background:var(--white)}
.card .img{position:absolute;left:2px}
.card .name{position:absolute;width:100%;font-size:7.5px;color:#666}
.card .cost{position:absolute;width:100%;font-weight:700;font-size:9px;color:#444}
.info{position:absolute;top:602px;height:56px;border:3px solid #e8e8e8;background:var(--white);display:flex;align-items:center;gap:8px;padding-left:10px}
.info h3{font-family:"Bitter",serif;color:var(--green);font-size:13px;border-bottom:1px solid var(--line)}
.info p{font-size:7px}
.footer{left:67px;top:1074px;width:563px;height:108px;background:var(--white);border:1px solid var(--line)}
.fcol{position:absolute;top:1090px}
.fcol ul{list-style:none;font-size:6.5px;margin-top:9px}
.fcol li{height:15.6px}
.fcol li::before{content:"• ";color:#999}
.social{display:flex;gap:6px;margin-top:12px}
.social i{width:18px;height:18px;border-radius:50%;background:#666}
.pay{left:353px;top:1141px;display:flex;gap:7px}
.pay i{width:23px;height:13px;border:1px solid #ddd;background:#eee}
.pay i:nth-child(2){background:#f2f2f2}
.pay i:nth-child(3){background:#1f4e9a}
.pay i:nth-child(4){background:#f8f8f8}
.bottom{left:69px;top:1189px;width:561px;display:flex;justify-content:space-between;font-size:6.5px;color:#666}
</style>
</head>
<body>
<div class="abs brand"><span class="brand-dot"></span>Fresh Pantry</div>
<div class="abs search">Search entire store here...
<svg width="11" height="11" viewBox="0 0 11 11"><circle cx="4.5" cy="4.5" r="3.5" fill="none" stroke="#4fb3c9" stroke-width="1.6"/><line x1="7" y1="7" x2="10" y2="10" stroke="#4fb3c9" stroke-width="1.8"/></svg></div>
<div class="abs cart-top"><svg width="14" height="11" viewBox="0 0 14 11"><path d="M1 3h12l-2 7H3z" fill="#4fb3c9"/></svg>(0 item) - <b>₦0.00</b> ▾</div>

<nav class="abs nav"><a>ALL</a><a>HEALTH &amp; WELLNESS</a><a>FRUITS &amp; VEGS</a><a>POULTRY, MEAT &amp; FISH</a><a>FOOD STUFFS</a><a>RECIPES</a><a>OTHERS</a></nav>
<div class="abs welcome"><span>Welcome to Pantrybasket.com. Feed well, live well</span><span>My Account | My Wishlist | My Cart | Checkout | Log in</span></div>

<div class="abs panel"></div>

<div class="photo hero" role="img" aria-label="Grilled steak with salad, tomatoes and potatoes"></div>
<div class="abs hero-cap"><h2>Fresh Natural Seafood</h2><p>Healthy food from the sea</p></div>
<div class="abs badge">40%</div>
<div class="abs dots"><i></i><i></i><i></i></div>
<div class="photo side1" role="img" aria-label="Sliced oranges"></div>
<div class="abs side1-text">Fee Delivery &amp;<br>Get <b>10%</b> Discount<br>Every registered users <b>100%</b></div>
<div class="photo side2" role="img" aria-label="Relaxing spa treatment with stones and flower"></div>
<div class="abs side2-cap">Herbal &amp; Ayurvedic &amp; Spa Products</div>

<div class="abs side-h teal" style="top:382px">CATEGORIES</div>
<ul class="abs cats">
<li>All</li><li>Health &amp; Wellness</li><li>Fruits &amp; Vegs<span>+</span></li><li>Poultry, Meat &amp; Fish<span>+</span></li><li>Food Stuffs<span>+</span></li><li>Recipes</li><li>Others<span>+</span></li>
</ul>
<div class="abs side-h" style="top:547px">MY CART</div>
<p class="abs side-note" style="top:581px">You have no items in your shopping cart.</p>
<div class="abs side-h" style="top:618px">COMPARE PRODUCTS</div>
<p class="abs side-note" style="top:652px">You have no items to compare.</p>
<div class="photo offer" role="img" aria-label="Basket of groceries, fruits, bread and milk"></div>
<div class="abs offer-h">Hurry Offer Ends Soon</div>
<div class="abs offer-pct">50%</div>
<div class="abs side-h" style="top:850px">LATEST PRODUCTS</div>
<div class="abs mini" style="top:886px"><div class="thumb" role="img" aria-label="Tilapia fish"></div><div>Frozen Tilapia (1kg)<br><span class="price">₦1,000.00</span><br>Add to Cart</div></div>
<div class="abs mini" style="top:940px"><div class="thumb" role="img" aria-label="Red snapper fillet" style="background:linear-gradient(135deg,#f0b8b8,#d96a6a)"></div><div>Red Snapper (1kg)<br><span class="price">₦1,000.00</span><br>Add to Cart</div></div>
<div class="abs mini" style="top:994px"><div class="thumb" role="img" aria-label="Croacker fish"></div><div>Frozen Croacker<br>(1kg)<br><span class="price">₦1,000.00</span><br>Add to Cart</div></div>

<div class="abs sec-h" style="left:207px;top:389px">LATEST PRODUCTS</div>
<div class="abs arrows"><i><svg width="6" height="6" viewBox="0 0 6 6"><path d="M4 0L1 3l3 3" stroke="#fff" fill="none"/></svg></i><i><svg width="6" height="6" viewBox="0 0 6 6"><path d="M2 0l3 3-3 3" stroke="#fff" fill="none"/></svg></i></div>

<div class="card" style="left:207px;top:416px;height:176px"><span class="ribbon">New</span><div class="photo img" role="img" aria-label="Grilled duck with salad" style="top:29px;width:119px;height:89px;background:linear-gradient(135deg,#8a5a3a,#6b8a3a)"></div><p class="name" style="top:126px">Frozen Tilapia (1kg)</p><p class="cost" style="top:141px">₦1,000.00</p></div>
<div class="card" style="left:346px;top:416px;height:176px"><span class="ribbon">New</span><div class="photo img" role="img" aria-label="Grilled steak with potatoes" style="top:29px;width:119px;height:89px;background:linear-gradient(135deg,#b08a3a,#5a2e1a 55%,#7a9a4a)"></div><p class="name" style="top:126px">Red Snapper (1kg)</p><p class="cost" style="top:141px">₦1,000.00</p></div>
<div class="card" style="left:485px;top:416px;height:176px"><span class="ribbon">New</span><div class="photo img" role="img" aria-label="Steak with onions and greens" style="top:29px;width:119px;height:89px;background:linear-gradient(135deg,#6a8a3a,#7a3a4a 50%,#4a3a2a)"></div><p class="name" style="top:126px">Frozen Croacker (1kg)</p><p class="cost" style="top:141px">₦1,000.00</p></div>

<div class="info" style="left:207px;width:199px">
<svg width="40" height="26" viewBox="0 0 40 26"><rect x="10" y="2" width="28" height="16" fill="none" stroke="#888" stroke-width="2"/><path d="M10 8H4L1 14v6h9" fill="none" stroke="#888" stroke-width="2"/><circle cx="8" cy="21" r="3" fill="#888"/><circle cx="30" cy="21" r="3" fill="#888"/></svg>
<div><h3>FREE SHIPPING</h3><p>On Order Over <b>$30</b> offer today</p></div></div>
<div class="info" style="left:415px;width:199px">
<svg width="30" height="30" viewBox="0 0 30 30"><rect x="2" y="4" width="8" height="22" rx="3" fill="none" stroke="#888" stroke-width="2"/><rect x="12" y="6" width="16" height="18" rx="2" fill="none" stroke="#888" stroke-width="2"/><path d="M16 11h8M16 15h8M16 19h8" stroke="#888" stroke-width="2"/></svg>
<div><h3>GIVE US CALL</h3><p>1-800-Pantry (1-800-555-0142)</p></div></div>

<div class="abs sec-h" style="left:207px;top:669px">FEATURED PRODUCTS</div>

<div class="card" style="left:207px;top:698px;height:164px"><span class="ribbon">New</span><div class="photo img" role="img" aria-label="Slice of carrot cake" style="top:0;width:119px;height:120px;background:linear-gradient(180deg,#b88a5a,#7a4a2a 60%,#6a6a6a)"></div><p class="name" style="top:122px">Sawa (500g)</p><p class="cost" style="top:138px">₦1,000.00</p></div>
<div class="card" style="left:346px;top:698px;height:164px"><span class="ribbon">New</span><div class="photo img" role="img" aria-label="Seafood platter with vegetables" style="top:0;width:119px;height:120px;background:linear-gradient(135deg,#f0d8c0,#e8906a 50%,#5a9a3a)"></div><p class="name" style="top:122px">Titus (500g)</p><p class="cost" style="top:138px">₦1,000.00</p></div>
<div class="card" style="left:485px;top:698px;height:164px"><span class="ribbon">New</span><div class="photo img" role="img" aria-label="Grocery basket with fruit, bread and milk" style="top:0;width:119px;height:120px;background:linear-gradient(135deg,#e8e0c8,#c89a5a 55%,#a07a3a)"></div><p class="name" style="top:122px">Frozen Tilapia (1kg)</p><p class="cost" style="top:138px">₦1,000.00</p></div>

<div class="card" style="left:207px;top:874px;height:164px"><span class="ribbon">New</span><div class="photo img" role="img" aria-label="Oranges, apples and citrus fruit" style="top:0;width:119px;height:120px;background:linear-gradient(135deg,#d84a3a,#f5a02a 45%,#f7b830)"></div><p class="name" style="top:122px">Panla (500g)</p><p class="cost" style="top:138px">₦1,000.00</p></div>
<div class="card" style="left:346px;top:874px;height:164px"><span class="ribbon">New</span><div class="photo img" role="img" aria-label="Breakfast of toast, bacon and fried eggs" style="top:0;width:119px;height:120px;background:linear-gradient(135deg,#d8a060,#c85a3a 50%,#f5d040 80%,#fff)"></div><p class="name" style="top:122px">Frozen Argentina (1kg)</p><p class="cost" style="top:138px">₦1,000.00</p></div>
<div class="card" style="left:485px;top:874px;height:164px"><span class="ribbon">New</span><div class="photo img" role="img" aria-label="Colourful macarons" style="top:0;width:119px;height:120px;background:linear-gradient(135deg,#8a7ab8,#e8d830 45%,#d83a5a)"></div><p class="name" style="top:122px">Frozen Croacker (1kg)</p><p class="cost" style="top:138px">₦1,000.00</p></div>

<div class="abs footer"></div>
<div class="fcol" style="left:82px"><div class="sec-h">CUSTOMER SERVICE</div><ul><li>About Us</li><li>Delivery Information</li><li>Privacy Policy</li><li>Term &amp; Condition</li></ul></div>
<div class="fcol" style="left:218px"><div class="sec-h">MY ACCOUNT</div><ul><li>My Product</li><li>My Orders</li><li>My Address</li><li>My Personal Info</li></ul></div>
<div class="fcol" style="left:353px"><div class="sec-h">FOLLOW ME</div><div class="social"><i></i><i></i></div></div>
<div class="abs pay"><i></i><i></i><i></i><i></i></div>

<div class="abs bottom"><span>Site Map | Search Terms | Advanced Search | Orders and Returns | Contact Us</span><span>© 2014 Pantrybasket.com Ltd</span></div>
</body>
</html>
```